TK Stationery - Modern Contemporary

Develop modern template for Letterhead and Stationery (business card, letterhead, envelopes) using the TK Logo and Icon

Colors
0054AA
0677BA
7BADD7
CADEEF
E8F1F8
00AB8E
00BBA5
67D7C9
C6EFE9
E9F9F6
EE7325
F08F49
F5BC92
FAE3D3
FDF4ED
6B429C
8869AF
B7A5CE
E3DAEB
F3F0F8

```html
<!DOCTYPE html>
<html lang="en">
<head>
<meta charset="utf-8">
<title>TK Stationery Letterhead</title>
<link href="https://fonts.googleapis.com/css2?family=Arimo:wght@400;700&family=Didact+Gothic&display=swap" rel="stylesheet">
<style>
  :root {
    --navy: #272a45;
    --green: #3db477;
    --orange: #ee7325;
    --text: #55575c;
    --heading: #4d4f54;
    --backdrop: #e6e6e8;
    --paper: #ffffff;
    --watermark: #f1f1f3;
    --watermark-dot: #fdf4ed;
  }
  * { box-sizing: border-box; margin: 0; padding: 0; }
  html, body { width: 1173px; height: 1200px; overflow: hidden; }
  body { background: var(--backdrop); font-family: "Arimo", Arial, sans-serif; }

  .letterhead {
    position: absolute; left: 162px; top: 0;
    width: 848px; height: 1200px;
    background: var(--paper); overflow: hidden;
  }

  /* Header */
  .header { position: absolute; left: 75px; top: 0; width: 697px; height: 123px; }
  .header-rule { position: absolute; left: 0; right: 0; top: 121px; height: 1.5px; background: var(--navy); }
  .brand { position: absolute; left: 0; top: 68px; display: flex; align-items: center; gap: 9px;
    font-size: 36px; line-height: 40px; font-weight: 700; color: var(--navy); letter-spacing: -0.4px; }
  .brand-dot { width: 10px; height: 10px; border-radius: 50%; background: var(--orange); }
  .divider { position: absolute; top: 74px; width: 1.5px; height: 35px; background: var(--navy); }
  .divider-contact { left: 316px; }
  .divider-address { left: 552px; }
  .contact { position: absolute; left: 352px; top: 74px; list-style: none;
    font-size: 13.5px; line-height: 17px; color: var(--navy); }
  .contact li { display: flex; align-items: center; gap: 9px; }
  .contact svg { width: 10px; height: 10px; fill: var(--green); flex: none; }
  .address { position: absolute; left: 584px; top: 74px; font-style: normal;
    font-size: 13.5px; line-height: 17px; color: var(--navy); }

  /* Faint decoration */
  .watermark { position: absolute; left: 280px; top: 870px; font-size: 330px; font-weight: 700;
    line-height: 1; color: var(--watermark); letter-spacing: -10px; }
  .watermark-dot { position: absolute; left: 797px; top: 845px; width: 50px; height: 50px;
    border-radius: 50%; background: var(--watermark-dot); }

  /* Letter body */
  .letter { position: absolute; left: 75px; top: 367px; width: 697px; color: var(--text); }
  .salutation { font-family: "Didact Gothic", "Century Gothic", sans-serif; font-size: 20px;
    font-weight: 400; line-height: 26px; letter-spacing: 0.3px; color: var(--heading);
    -webkit-text-stroke: 0.6px var(--heading); margin-left: 2px; margin-bottom: 46px; }
  .letter p { font-size: 14.8px; line-height: 17.6px; margin-bottom: 14px; }
  .letter .closing { font-family: "Didact Gothic", "Century Gothic", sans-serif; font-size: 11px;
    line-height: 14px; color: #3f4146; -webkit-text-stroke: 0.3px #3f4146;
    margin-top: 36px; margin-left: 2px; }
  .signature { width: 138px; height: 38px; margin-top: 34px; margin-left: 1px;
    background: linear-gradient(90deg, #ececee, #f4f4f6); border-radius: 4px; }

  /* Footer */
  .footer { position: absolute; left: 0; bottom: 0; width: 848px; height: 39px; }
  .footer svg { position: absolute; inset: 0; width: 100%; height: 100%; }
  .footer-url { position: absolute; left: 75px; top: 9px; font-size: 17.5px; line-height: 22px;
    font-weight: 700; color: #fff; }
</style>
</head>
<body>
  <main class="letterhead">
    <header class="header">
      <div class="brand">TK Stationery<span class="brand-dot"></span></div>
      <span class="divider divider-contact"></span>
      <ul class="contact">
        <li><svg viewBox="0 0 10 10"><path d="M2 0.5 L3.6 2.6 L2.8 3.6 Q4 6 6.4 7.2 L7.4 6.4 L9.5 8 L8.4 9.5 Q4 9 0.5 1.6 Z"/></svg>555-010-2100</li>
        <li><svg viewBox="0 0 10 10"><path d="M0 2 H10 V8.5 H0 Z M0.6 2.4 L5 5.8 L9.4 2.4" stroke="#fff" stroke-width="0.8"/></svg>hello@tkstationery.com</li>
      </ul>
      <span class="divider divider-address"></span>
      <address class="address">Your address, city<br>state, ZIP 0000</address>
      <span class="header-rule"></span>
    </header>

    <div class="watermark" aria-hidden="true">TK</div>
    <div class="watermark-dot" aria-hidden="true"></div>

    <section class="letter">
      <h1 class="salutation">Dear Mr. Carter,</h1>
      <p>Lorem ipsum dolor sit amet, consectetuer adipiscing elit, sed diam nonmmy nibh euismod tincidunt ut laor eet dolore magna aliquam erat volutpat. Ut wisi enim ad minim veniam, quis nostrud exerci tationmcorper suscipit lobortis nisl ut aliquip ex ea commodo consequat. Duis autem vel eum iriure dolor in hendrerit in vulputate velit esse molestie consequat, vel illum dolore eu feugiat</p>
      <p>Rorem ipsum dolor sit amet, consectetuer adipiscing elit, sed diam nonmmy nibh euismod tincidunt ut laor eet dolore magna aliquam erat volutpat. Ut wisi enim ad minim veniam, quis nostrud exerci tationmcorper suscipit lobortis nisl ut aliquip ex ea commodo consequat. Duis autem vel eum iriure dolor in hendrerit in vulputate velit esse molest</p>
      <p>Dorem ipsum dolor sit amet, consectetuer adipiscing elit, sed diam nonmmy nibh euismod tincidunt ut laor eet dolore magna aliquam erat volutpat. Ut wisi enim ad minim veniam, quis nostrud exerci tationmcorper suscipit lobortis nisl ut aliquip ex ea commodo consequat. Duis autem vel eum iriure dolor in hendrerit in suscipit lobortis nisl ut aliquip ex ea commodo consequat. Duis autem vel eum iriure dolor in hendrerit in vulputate velit esse molestie consequat, vel illum</p>
      <p>Sorem ipsum dolor sit amet, consectetuer adipiscing elit, sed diam nonmmy nibh euismod tincidunt ut laor eet dolore magna aliquam erat volutpat. Ut wisi enim ad minim veniam, quis nostrud exerci tationmcorper suscipit lobortis nisl ut aliquip ex ea commodo consequat. Duis autem vel eum iriure dolor in</p>
      <p class="closing">Sincerely,</p>
      <div class="signature" role="img" aria-label="Handwritten signature of the sender"></div>
    </section>

    <footer class="footer">
      <svg viewBox="0 0 848 39" preserveAspectRatio="none" aria-hidden="true">
        <path d="M0 0 H285 Q298 0 306 7 L322 21 Q330 26 345 26 H848 V39 H0 Z" fill="var(--green)"/>
        <path d="M314 8 H563 L568 14 H321 Z" fill="var(--orange)"/>
        <path d="M567 8 H848 V14 H573 Z" fill="var(--navy)"/>
      </svg>
      <span class="footer-url">www.tkstationery.com</span>
    </footer>
  </main>
</body>
</html>
```